Business Card Design Project

We are a construction company in Orange County, CA. We need a two sided business card. We would like the back to be our logo with web URL. Front should included Name, title, address, phone, fax and email address.

our address is
627 West Dorrance Blvd, Suite 308
Anaheim, CA 92718

Our logo files are attached.

Construction

```html
<!DOCTYPE html>
<html lang="en">
<head>
<meta charset="utf-8">
<title>Trelvon Business Card</title>
<link rel="stylesheet" href="https://fonts.googleapis.com/css2?family=Source+Sans+3:wght@400;600;700&display=swap">
<style>
  :root {
    --brand-blue: #1b4c82;
    --ink: #3a3a3a;
    --card: #ffffff;
    --backdrop: #ececec;
    --card-edge: #3b3b3b;
    --bar-dark: #262626;
    --bar-light: #cfcfcf;
  }
  * { margin: 0; padding: 0; box-sizing: border-box; }
  html, body {
    width: 1200px;
    height: 997px;
    overflow: hidden;
    background: var(--backdrop);
    font-family: "Source Sans 3", "Myriad Pro", sans-serif;
  }
  .canvas { position: relative; width: 1200px; height: 997px; }

  .card {
    position: absolute;
    width: 749px;
    height: 428px;
    background: var(--card);
    border: 1.5px solid var(--card-edge);
    border-radius: 20px;
    overflow: hidden;
  }
  .card--front { left: 74px; top: 53px; }
  .card--back { left: 383px; top: 507px; }

  .brand-name {
    position: absolute;
    left: 0; right: 0;
    text-align: center;
    font-weight: 700;
    color: var(--brand-blue);
    font-size: 112px;
    line-height: 1;
    letter-spacing: 1px;
  }
  .card--front .brand-name { top: 48px; }
  .card--back .brand-name { top: 126px; }

  .holder {
    position: absolute;
    top: 218px; left: 0; right: 0;
    text-align: center;
    color: var(--brand-blue);
    font-size: 26px;
  }
  .holder__name { font-weight: 700; }
  .holder__title { font-weight: 400; }

  .contacts {
    position: absolute;
    top: 258px; left: 0; right: 0;
    display: flex;
    justify-content: center;
    gap: 14px;
    color: var(--ink);
    font-size: 19px;
  }
  .contact { display: flex; align-items: center; gap: 6px; }
  .contact svg { width: 16px; height: 16px; fill: var(--ink); }

  .address {
    position: absolute;
    top: 305px; left: 0; right: 0;
    text-align: center;
    color: var(--ink);
    font-size: 19px;
  }

  .footer-band { position: absolute; left: 0; bottom: 0; width: 749px; height: 42px; }

  .web-front {
    position: absolute;
    bottom: 8px; left: 424px; width: 310px;
    text-align: center;
    color: #ffffff;
    font-size: 19px;
    letter-spacing: 3px;
  }
  .web-back {
    position: absolute;
    top: 286px; left: 0; right: 0;
    text-align: center;
    color: var(--ink);
    font-size: 21px;
    letter-spacing: 4px;
  }
</style>
</head>
<body>
<main class="canvas">

  <section class="card card--front" aria-label="Card front">
    <div class="brand-name">TRELVON</div>

    <p class="holder"><span class="holder__name">Your Name,</span> <span class="holder__title">Title</span></p>

    <div class="contacts">
      <span class="contact">
        <svg viewBox="0 0 16 16" aria-hidden="true"><path d="M3.5 1.5l2.5 2.8-1.3 1.9c.9 2 2.4 3.5 4.4 4.4l1.9-1.3 2.8 2.5-1.6 2.3C7.2 14 2 8.8 1.2 3.1z"/></svg>
        01-234-5678
      </span>
      <span class="contact">
        <svg viewBox="0 0 16 16" aria-hidden="true"><path d="M4 1h8v4H4zM1 6h14v6h-2v3H3v-3H1zm4 4v3h6v-3z"/></svg>
        01-234-5678
      </span>
      <span class="contact">
        <svg viewBox="0 0 16 16" aria-hidden="true"><path d="M1 4h14v9H1zm1 1l6 4 6-4z" fill-rule="evenodd"/></svg>
        info@trelvon.com
      </span>
    </div>

    <p class="address">627 West Dorrance Blvd, Suite 308, Anaheim, CA&nbsp; 92718</p>

    <svg class="footer-band" viewBox="0 0 749 42" aria-hidden="true">
      <defs>
        <linearGradient id="bar-fade" x1="0" x2="1" y1="0" y2="0">
          <stop offset="0" stop-color="var(--bar-dark)"/>
          <stop offset="0.55" stop-color="#6a6a6a"/>
          <stop offset="1" stop-color="var(--bar-light)"/>
        </linearGradient>
      </defs>
      <polygon points="0,19 406,19 398,42 0,42" fill="url(#bar-fade)"/>
      <polygon points="424,0 749,0 749,42 408,42" fill="var(--brand-blue)"/>
    </svg>
    <p class="web-front">www.trelvon.com</p>
  </section>

  <section class="card card--back" aria-label="Card back">
    <div class="brand-name">TRELVON</div>
    <p class="web-back">www.trelvon.com</p>
  </section>

</main>
</body>
</html>
```